Heritage Hollow Business Cards

Require a business card design. <br/><br/>Needs to include logo (either round or long version) plus these details:<br/>Maya Torvell<br/>Heritage Hollow<br/>maya@kelvadtrading.com.au<br/>02 6481 7395<br/>PO Box Glenwarra NSW 2791<br/>www.heritagehollow.com.au<br/><br/>I need in an editable format so that I can create for multiple staff members. <br/><br/>

Target Market(s)

We are an online store selling renovation products to home owners are builders. Looking for a classic classy design.

Industry/Entity Type

Home And Garden

Contact Information for Business Card

Maya Torvell
Heritage Hollow
maya@kelvadtrading.com.au
02 6481 7395
PO Box Glenwarra NSW 2791
www.heritagehollow.com.au

Colors

Designer to choose colors to be used in the design.

Requirements
Must have
• Must include Logo.

```html
<!DOCTYPE html>
<html lang="en">
<head>
<meta charset="utf-8">
<title>Heritage Hollow Business Cards</title>
<link rel="stylesheet" href="https://fonts.googleapis.com/css2?family=Josefin+Slab:wght@400;600&display=swap">
<style>
  :root {
    --backdrop: #8c8c8c;
    --cream: #fdfcef;
    --charcoal: #2a2828;
    --ink: #2d2b2b;
    --muted: #8e8b86;
    --white: #ffffff;
  }
  * { margin: 0; padding: 0; box-sizing: border-box; }
  html, body {
    width: 1200px; height: 960px; overflow: hidden;
    background: var(--backdrop);
    font-family: "Josefin Slab", Georgia, serif;
  }
  .canvas { position: relative; width: 1200px; height: 960px; }
  .card {
    position: absolute; left: 245px; width: 710px; height: 404px;
  }
  .card-front {
    top: 36px; background: var(--cream);
    border: 9px solid var(--charcoal);
  }
  .card-back {
    top: 520px; background: var(--charcoal);
    border: 8px solid var(--white);
  }
  .front-brand {
    position: absolute; left: 64px; top: 54px;
    display: flex; align-items: center; gap: 12px;
  }
  .brand-dot {
    width: 26px; height: 26px; border-radius: 50%;
    border: 1.5px solid var(--ink);
  }
  .brand-name {
    font-size: 35px; font-weight: 600; color: var(--ink);
    letter-spacing: 0.2px;
  }
  .contact {
    position: absolute; left: 64px; top: 150px;
    font-size: 17px; color: var(--muted); letter-spacing: 0.5px;
  }
  .contact .company { color: var(--ink); }
  .contact .address { margin-top: 6px; }
  .contact-list { list-style: none; margin-top: 12px; }
  .contact-list li {
    display: flex; align-items: center; gap: 8px; height: 26px;
  }
  .contact-list svg { width: 14px; height: 14px; flex: none; }
  .staff {
    position: absolute; right: 58px; top: 278px; text-align: right;
  }
  .staff-name {
    font-size: 27px; font-weight: 600; color: var(--ink); letter-spacing: 0.5px;
  }
  .staff-role {
    font-size: 18px; color: var(--muted); margin-top: 6px; letter-spacing: 0.5px;
  }
  .back-mark {
    position: absolute; left: 232px; top: 65px;
    width: 246px; height: 246px; border-radius: 50%;
    border: 1.5px solid var(--white);
    display: flex; align-items: center; justify-content: center;
  }
  .back-name {
    font-size: 36px; font-weight: 600; color: var(--white);
    text-align: center; line-height: 1.05;
  }
</style>
</head>
<body>
<main class="canvas">
  <section class="card card-front" aria-label="Business card front">
    <div class="front-brand">
      <span class="brand-dot"></span>
      <span class="brand-name">Heritage Hollow</span>
    </div>
    <div class="contact">
      <p class="company">Heritage Hollow</p>
      <p class="address">PO Box Glenwarra NSW 2791</p>
      <ul class="contact-list">
        <li>
          <svg viewBox="0 0 14 14" aria-hidden="true"><path d="M3 1.5 L5 1.5 L5.5 4 L4 5 Q5 8 9 10 L10 8.5 L12.5 9 L12.5 11 Q12 12.5 10 12.5 Q2 11 1.5 3.5 Q1.5 1.8 3 1.5 Z" fill="var(--ink)"/></svg>
          <span>02 6481 7395</span>
        </li>
        <li>
          <svg viewBox="0 0 14 14" aria-hidden="true"><rect x="1" y="3" width="12" height="8" fill="var(--ink)"/><path d="M1 3 L7 8 L13 3" fill="none" stroke="var(--cream)" stroke-width="1"/></svg>
          <span>maya@kelvadtrading.com.au</span>
        </li>
        <li>
          <svg viewBox="0 0 14 14" aria-hidden="true"><g fill="none" stroke="var(--ink)" stroke-width="1.1"><circle cx="7" cy="7" r="5.8"/><ellipse cx="7" cy="7" rx="2.6" ry="5.8"/><path d="M1.2 7 H12.8 M2.2 4 H11.8 M2.2 10 H11.8"/></g></svg>
          <span>www.heritagehollow.com.au</span>
        </li>
      </ul>
    </div>
    <div class="staff">
      <p class="staff-name">MAYA TORVELL</p>
      <p class="staff-role">Founder &amp; CEO</p>
    </div>
  </section>

  <section class="card card-back" aria-label="Business card back">
    <div class="back-mark">
      <p class="back-name">Heritage<br>Hollow</p>
    </div>
  </section>
</main>
</body>
</html>
```